Upstart Retirement Planning Firm needs help with business card design

Harborview Nest Advisors, LLC is looking for help with business card design. We give advice on investments, insurance, and other financial matters related to retirement. There are some required disclosures that we will provide but mostly we are looking for a professional, classy business card that reflects the theme we have chosen. We have a logo that is attached but we would like to add a phrase; "Shaping Your Working Years Into Lasting Comfort"

Doubled sided only so that we can add the required disclosures (needed for our industry) on the back of the card. We will provide the exact words for this in 1-2 days.

Target Market(s)

Retirees and Pre-retirees. Professionals 50+ years old

Industry/Entity Type

Financial Planning

Contact Information for Business Card

We currently have two people who will need separate cards so we'd like to have a template so that we can add names for new cards in the future.

For the first run, please show the following information.

Gregor Pelham, MBA, ChFC®, CLU®
Financial Advisor, Registered Representative
gpelham@harborviewnest.example
Phone: (555) 318-2946
Toll Free Fax: (800) 555-0193

Address is
2187 Meadowlark Ridge Rd.
Suite K418
Maple Harbor, NC 23999

Colors
3277b5

Requirements
Must have
• Logo, contact info, small phase to describe business (in description), required legal disclosures on back of the card as follows (in small font)
• Gregor Pelham is a registered representative of and offers securities through Brightmoor Capital Brokerage Corporation, Member FNQX. Brightmoor Capital Brokerage Corporation is a member of the Brightmoor Capital Alliance which is the marketing name for Brightmoor Holding Corporation and its affiliates.
Nice to have
• Rounded edges, raised letters
Should not have
• any colors that aren't in the logo (other than black for font)

```html
<!DOCTYPE html>
<html lang="en">
<head>
<meta charset="utf-8">
<title>Harborview Nest Advisors – Business Cards</title>
<link rel="stylesheet" href="https://fonts.googleapis.com/css2?family=Arimo:wght@400;700&display=swap">
<style>
  :root {
    --brand-blue: #1774bf;
    --brand-blue-deep: #0f67b1;
    --paper-white: #ffffff;
    --divider-grey: #b9bcc0;
    --stage: #ececec;
  }
  * { box-sizing: border-box; margin: 0; padding: 0; }
  html, body {
    width: 1200px; height: 750px; overflow: hidden;
    background: var(--stage);
    font-family: "Arimo", Arial, sans-serif;
  }
  .sheet {
    width: 1200px; height: 750px;
    display: flex; align-items: center; justify-content: center; gap: 40px;
  }
  .card {
    position: relative;
    width: 540px; height: 309px;
    border-radius: 10px;
    overflow: hidden;
    box-shadow: 0 6px 18px rgba(0,0,0,.18);
  }

  /* Brand side */
  .card--brand {
    background: var(--brand-blue);
    color: var(--paper-white);
    display: flex; flex-direction: column; align-items: center; justify-content: center;
  }
  .brand-name {
    font-weight: 700; font-size: 30px; letter-spacing: .5px;
    display: flex; align-items: center; gap: 12px;
  }
  .brand-dot { width: 14px; height: 14px; border-radius: 50%; background: var(--paper-white); }
  .tagline { margin-top: 42px; font-size: 13px; letter-spacing: .3px; }

  /* Contact side */
  .card--contact { background: var(--brand-blue); color: var(--paper-white); }
  .contact-shape { position: absolute; inset: 0; width: 100%; height: 100%; }
  .contact-logo {
    position: absolute; left: 330px; top: 118px; width: 200px;
    color: var(--brand-blue-deep); font-weight: 700; font-size: 19px; line-height: 1.25;
    text-align: center;
  }
  .contact-details { position: absolute; left: 28px; top: 36px; width: 280px; }
  .person-name { font-size: 18px; font-weight: 700; }
  .person-name .credentials { font-size: 10px; }
  .person-role { font-size: 11.5px; line-height: 1.35; margin-top: 4px; }
  .address { font-size: 12px; line-height: 1.45; margin-top: 40px; }
  .contact-lines { list-style: none; font-size: 12px; line-height: 1.55; margin-top: 2px; }
  .contact-lines li { display: flex; align-items: center; gap: 7px; white-space: nowrap; }
  .contact-lines svg { width: 12px; height: 12px; fill: var(--paper-white); flex: none; }
</style>
</head>
<body>
<main class="sheet">
  <section class="card card--brand" aria-label="Business card, brand side">
    <div class="brand-name"><span class="brand-dot"></span>Harborview Nest Advisors</div>
    <p class="tagline">Shaping Your Working Years Into Lasting Comfort</p>
  </section>

  <section class="card card--contact" aria-label="Business card, contact side">
    <svg class="contact-shape" viewBox="0 0 540 309" preserveAspectRatio="none" aria-hidden="true">
      <path d="M540 0 L296 0 Q310 215 476 309 L540 309 Z" fill="#ffffff"/>
      <path d="M290 0 Q304 218 466 309" fill="none" stroke="#b9bcc0" stroke-width="4"/>
    </svg>

    <div class="contact-logo">Harborview Nest Advisors, LLC</div>

    <div class="contact-details">
      <h1 class="person-name">Gregor Pelham, <span class="credentials">MBA, ChFC®, CLU®</span></h1>
      <p class="person-role">Financial Advisor<br>Registered Representative</p>
      <p class="address">2187 Meadowlark Ridge Rd.<br>Suite K418<br>Maple Harbor, NC 23999</p>
      <ul class="contact-lines">
        <li><svg viewBox="0 0 24 24"><path d="M6.6 10.8a15 15 0 0 0 6.6 6.6l2.2-2.2a1 1 0 0 1 1-.25 11.4 11.4 0 0 0 3.6.57 1 1 0 0 1 1 1V20a1 1 0 0 1-1 1A17 17 0 0 1 3 4a1 1 0 0 1 1-1h3.5a1 1 0 0 1 1 1c0 1.25.2 2.45.57 3.6a1 1 0 0 1-.25 1z"/></svg>(555) 318-2946</li>
        <li><svg viewBox="0 0 24 24"><path d="M6.6 10.8a15 15 0 0 0 6.6 6.6l2.2-2.2a1 1 0 0 1 1-.25 11.4 11.4 0 0 0 3.6.57 1 1 0 0 1 1 1V20a1 1 0 0 1-1 1A17 17 0 0 1 3 4a1 1 0 0 1 1-1h3.5a1 1 0 0 1 1 1c0 1.25.2 2.45.57 3.6a1 1 0 0 1-.25 1z"/></svg>(800) 555-0193 (Toll Free)</li>
        <li><svg viewBox="0 0 24 24"><path d="M2 5h20v14H2z M3.5 6.5 12 13l8.5-6.5" fill="#ffffff"/><path d="M3.5 6.5 12 13l8.5-6.5" fill="none" stroke="#1774bf" stroke-width="1.6"/></svg>gpelham@harborviewnest.example</li>
      </ul>
    </div>
  </section>
</main>
</body>
</html>
```